Business Card Design

We need a design for business cards for our company. We have a logo. We teach EMT's and we are based out of Virginia. The information that will need to add would be, name, title, phone number, email, address. On the back of the business card would be "We help you, help others"

Target Market(s)

People that want to become EMT's

Colors

Designer to choose colors to be used in the design.

Requirements
Must have
• company logo

```html
<!DOCTYPE html>
<html lang="en">
<head>
<meta charset="utf-8">
<title>Crest Response Training – Business Card</title>
<link href="https://fonts.googleapis.com/css2?family=Lato:wght@400;700&display=swap" rel="stylesheet">
<style>
  :root{
    --backdrop:#2b2b2b;
    --card:#1f2b36;
    --red:#e8283f;
    --steel:#7a8a95;
    --white:#f2f4f6;
    --muted:#c9d0d5;
  }
  *{margin:0;padding:0;box-sizing:border-box}
  html,body{width:1200px;height:900px;overflow:hidden;background:var(--backdrop)}
  body{font-family:'Lato',sans-serif;position:relative}
  .card{
    position:absolute;left:250px;width:700px;height:400px;
    background:var(--card);overflow:hidden;
  }
  .card--front{top:30px}
  .card--back{top:470px}
  .edge-band{position:absolute;left:0;bottom:0;width:700px;height:34px}
  .brand{
    position:absolute;display:flex;align-items:center;gap:14px;
    color:var(--red);font-weight:400;letter-spacing:1px;white-space:nowrap;
  }
  .brand__dot{width:18px;height:18px;border-radius:50%;background:var(--red);flex:none}
  .card--front .brand{left:50%;top:150px;transform:translateX(-50%);font-size:38px}
  .card--back .brand{left:50%;top:105px;transform:translateX(-50%);font-size:32px}
  .tagline{
    position:absolute;right:150px;bottom:70px;
    color:var(--white);font-size:15px;letter-spacing:.5px;
  }
  .contact-block{
    position:absolute;left:180px;top:240px;display:flex;align-items:center;
  }
  .person{text-align:right;padding-right:22px}
  .person__name{color:var(--red);font-size:19px;letter-spacing:.5px}
  .person__name strong{font-weight:700}
  .person__role{color:var(--white);font-size:13px;margin-top:2px}
  .divider{width:1px;height:72px;background:var(--steel)}
  .details{list-style:none;padding-left:22px;font-size:13px;color:var(--white);line-height:1.75}
  .details li{display:flex;align-items:center;gap:8px}
  .details svg{width:12px;height:12px;flex:none}
  .details .web{color:var(--red);padding-left:20px}
</style>
</head>
<body>

<section class="card card--front">
  <div class="brand"><span class="brand__dot"></span>CREST RESPONSE TRAINING</div>
  <p class="tagline">WE HELP YOU, HELP OTHERS</p>
  <svg class="edge-band" viewBox="0 0 700 34" preserveAspectRatio="none" aria-hidden="true">
    <rect x="0" y="22" width="700" height="12" fill="var(--steel)"/>
    <path d="M430 34 C430 14 440 8 460 8 L700 0 L700 34 Z" fill="var(--red)"/>
  </svg>
</section>

<section class="card card--back">
  <div class="brand"><span class="brand__dot"></span>CREST RESPONSE TRAINING</div>
  <div class="contact-block">
    <div class="person">
      <p class="person__name"><strong>DANA</strong> WHITFIELD</p>
      <p class="person__role">Founder / Director</p>
    </div>
    <span class="divider"></span>
    <ul class="details">
      <li><svg viewBox="0 0 12 12"><path d="M2 1h3l1 3-1.5 1a6 6 0 0 0 2.5 2.5L8 6l3 1v3a1 1 0 0 1-1 1A9 9 0 0 1 1 2a1 1 0 0 1 1-1z" fill="var(--red)"/></svg>+1 540 555 0187</li>
      <li><svg viewBox="0 0 12 12"><rect x="0.5" y="2" width="11" height="8" rx="1" fill="var(--red)"/><path d="M1 3l5 4 5-4" stroke="var(--card)" fill="none"/></svg>info@crestresponse.com</li>
      <li class="web">www.crestresponse.com</li>
    </ul>
  </div>
  <svg class="edge-band" viewBox="0 0 700 34" preserveAspectRatio="none" aria-hidden="true">
    <rect x="0" y="22" width="700" height="12" fill="var(--steel)"/>
    <path d="M430 34 C430 14 440 8 460 8 L700 0 L700 34 Z" fill="var(--red)"/>
  </svg>
</section>

</body>
</html>
```